Mira Bloom Fitness Coaching Project

I am a personal trainer based in London. My services include one-on-one PT sessions, bootcamps.
I would like the design to be minimalistic. With light colours: white, pink, purple.
I specialise in weight loss, flexibility, mobility.

Tessa Brogan
Personal Trainer
Email: tessa.brogan@quellmail.com
tel: 07700218493
Pictogram: Mira Bloom

Target Market(s)

adults, mostly females (age 18-50).

Industry/Entity Type

MIRA BLOOM

Contact Information for Business Card

Tessa Brogan
Personal Trainer
tel: 07700218493
Pictogram: Mira Bloom

Font styles to use
Serif

Colors
eea4c8
fbd4d5
fdf9cf
cfeae6
cee9f5

Requirements
Nice to have
• minimalistic style
• easy to read and remember

```html
<!DOCTYPE html>
<html lang="en">
<head>
<meta charset="utf-8">
<title>Mira Bloom Fitness Coaching – Business Card</title>
<link rel="stylesheet" href="https://fonts.googleapis.com/css2?family=Oswald:wght@500;600&family=Open+Sans:ital,wght@0,400;1,400&display=swap">
<style>
  :root {
    --canvas-bg: #e9e7e4;
    --cream: #fdf9cf;
    --blush: #fbd4d5;
    --rose: #eea4c8;
    --dash-pink: #e9a5cf;
    --badge-grey: #e8e8e8;
    --ink: #111111;
    --white: #ffffff;
  }
  * { margin: 0; padding: 0; box-sizing: border-box; }
  html, body {
    width: 1200px; height: 1000px; overflow: hidden;
    background: var(--canvas-bg);
  }
  .canvas { position: relative; width: 1200px; height: 1000px; }

  .card {
    position: absolute; left: 277px; width: 648px; height: 398px;
    overflow: hidden; box-shadow: 0 2px 10px rgba(0,0,0,0.18);
  }
  .card--front { top: 50px; }
  .card--back { top: 548px; height: 392px; background: var(--white); }

  .front__top { position: absolute; inset: 0 0 auto 0; height: 191px; background: var(--cream); }
  .front__bottom { position: absolute; inset: 191px 0 0 0; background: var(--blush); }

  .badge { position: absolute; }
  .badge--front { left: 203px; top: 35px; width: 260px; height: 260px; }
  .badge--back { left: -55px; top: -10px; width: 230px; height: 220px; }
  .badge__name {
    font-family: "Oswald", sans-serif; font-weight: 600;
    fill: var(--ink); letter-spacing: 1px;
  }

  .front__email {
    position: absolute; left: 0; right: 0; top: 300px; text-align: center;
    font-family: "Open Sans", sans-serif; font-size: 12.5px;
    letter-spacing: 3.4px; color: var(--ink);
  }

  .back__panel {
    position: absolute; left: 337px; top: 0; right: 0; bottom: 0;
    background: var(--rose);
  }
  .identity { position: absolute; left: 56px; top: 218px; width: 240px; text-align: right; }
  .identity__name {
    font-family: "Oswald", sans-serif; font-weight: 600; font-size: 47px;
    line-height: 1; color: var(--ink); text-align: left; white-space: nowrap;
  }
  .identity__role {
    font-family: "Open Sans", sans-serif; font-style: italic; font-size: 17px;
    color: var(--ink); margin-top: 2px;
  }

  .contacts { position: absolute; left: 348px; top: 88px; list-style: none; }
  .contacts__item {
    display: flex; align-items: center; height: 24px; margin-bottom: 46px;
    font-family: "Open Sans", sans-serif; font-size: 16.5px; color: var(--white);
  }
  .contacts__icon { width: 24px; height: 24px; margin-right: 24px; flex: none; }
</style>
</head>
<body>
<main class="canvas">

  <section class="card card--front" aria-label="Card front">
    <div class="front__top"></div>
    <div class="front__bottom"></div>
    <svg class="badge badge--front" viewBox="0 0 260 260">
      <rect x="45" y="45" width="170" height="170" fill="none" stroke="var(--dash-pink)" stroke-width="4" stroke-dasharray="14 9" transform="rotate(43 130 130)"/>
      <rect x="57" y="57" width="146" height="146" fill="var(--badge-grey)" transform="rotate(43 130 130)"/>
      <text class="badge__name" x="130" y="140" font-size="22" text-anchor="middle">MIRA BLOOM</text>
    </svg>
    <p class="front__email">tessa.brogan@quellmail.com</p>
  </section>

  <section class="card card--back" aria-label="Card back">
    <svg class="badge badge--back" viewBox="0 0 230 220">
      <rect x="38" y="33" width="150" height="150" fill="none" stroke="var(--dash-pink)" stroke-width="4" stroke-dasharray="14 9" transform="rotate(43 113 108)"/>
      <rect x="55" y="50" width="116" height="116" fill="var(--badge-grey)" transform="rotate(43 113 108)"/>
      <text class="badge__name" x="125" y="115" font-size="17" text-anchor="middle">MIRA BLOOM</text>
    </svg>

    <div class="identity">
      <h1 class="identity__name">Tessa Brogan</h1>
      <p class="identity__role">Personal Trainer</p>
    </div>

    <div class="back__panel"></div>

    <ul class="contacts">
      <li class="contacts__item">
        <svg class="contacts__icon" viewBox="0 0 24 24" aria-hidden="true">
          <path fill="var(--white)" d="M6.6 3.5l2.6 3.4c.4.5.3 1.1-.1 1.5L7.7 9.6c1 2.5 3.9 5.5 6.6 6.7l1.3-1.4c.4-.4 1-.5 1.5-.1l3.4 2.6c.5.4.6 1.1.1 1.6l-1.6 1.8c-.8.9-2.2 1.1-3.5.6C9.4 19.4 4.9 14.9 3 9.4c-.5-1.3-.3-2.7.6-3.5l1.5-1.4c.4-.5 1.1-.5 1.5 0z"/>
        </svg>
        07700218493
      </li>
      <li class="contacts__item">
        <svg class="contacts__icon" viewBox="0 0 24 24" aria-hidden="true">
          <circle cx="12" cy="12" r="10" fill="var(--white)"/>
        </svg>
        www.Pictogram/ Mira Bloom
      </li>
      <li class="contacts__item">
        <svg class="contacts__icon" viewBox="0 0 24 24" aria-hidden="true">
          <rect x="2" y="5" width="20" height="14" fill="none" stroke="var(--white)" stroke-width="2"/>
          <path d="M2 5l10 8 10-8M2 19l7-7M22 19l-7-7" fill="none" stroke="var(--white)" stroke-width="2"/>
        </svg>
        tessa.brogan@quellmail.com
      </li>
    </ul>
  </section>

</main>
</body>
</html>
```